Heron Loan Partners Business Card

We need a business card design for our mortgage servicing company. In addition to servicing the loans of homeowners, we help homeowners with purchasing their homes and any mortgage refinancing. We would like to see designs that use the colors in the logo attached below (gold-ish yellow and navy blue), and any other design you deem fit! The design should communicate a simpler life with smart mortgages provided by Heron.

```html
<!DOCTYPE html>
<html lang="en">
<head>
<meta charset="utf-8">
<title>Heron Loan Partners Business Card</title>
<link href="https://fonts.googleapis.com/css2?family=Playfair+Display:wght@700&family=Poppins:wght@400;500&display=swap" rel="stylesheet">
<style>
  :root {
    --navy: #262b3a;
    --navy-deep: #1f1d4a;
    --gold: #e2b53e;
    --paper: #ffffff;
    --canvas: #f4f4f4;
    --text-dark: #1e2030;
  }
  * { margin: 0; padding: 0; box-sizing: border-box; }
  html, body { width: 1048px; height: 1200px; overflow: hidden; background: var(--canvas); }
  .stage { position: relative; width: 1048px; height: 1200px; }
  .card {
    position: absolute; left: 104px; width: 840px; height: 480px; overflow: hidden;
    box-shadow: 0 14px 40px rgba(0,0,0,0.22);
  }
  .card--front { top: 80px; background: var(--navy); }
  .card--back { top: 640px; background: var(--paper); }
  .card svg.shapes { position: absolute; inset: 0; }
  .texture {
    position: absolute; inset: 0;
  }
  .card--front .texture {
    background: radial-gradient(ellipse at 50% 40%, #323849 0%, var(--navy) 70%);
  }
  .card--back .texture {
    background: radial-gradient(ellipse at 85% 30%, #ececec 0%, var(--paper) 60%);
  }
  .brand-name {
    position: absolute; font-family: "Playfair Display", serif; font-weight: 700; color: var(--gold);
    line-height: 1;
  }
  .card--front .brand-name { left: 0; right: 0; top: 150px; text-align: center; font-size: 112px; }
  .card--back .brand-name { left: 530px; width: 240px; top: 232px; text-align: center; font-size: 58px; }
  .web {
    position: absolute; font-family: "Playfair Display", serif; font-weight: 700; color: var(--navy-deep);
    line-height: 1;
  }
  .card--front .web { left: 115px; width: 590px; top: 390px; text-align: center; font-size: 30px; letter-spacing: 9px; }
  .card--back .web { left: 46px; top: 436px; font-size: 26px; letter-spacing: 5.5px; }
  .holder { position: absolute; left: 122px; top: 36px; }
  .holder-name {
    font-family: "Playfair Display", serif; font-weight: 700; font-size: 44px; color: var(--navy-deep); line-height: 1.05;
  }
  .holder-title {
    font-family: "Poppins", sans-serif; font-weight: 500; font-size: 17px; letter-spacing: 3.5px; color: var(--navy-deep);
  }
  .contact-list { position: absolute; left: 122px; top: 0; list-style: none; }
  .contact-item {
    position: absolute; left: 0; width: 320px; font-family: "Poppins", sans-serif; font-size: 19px;
    color: var(--text-dark); line-height: 1.25; transform: translateY(-50%);
  }
</style>
</head>
<body>
<main class="stage">

  <section class="card card--front" aria-label="Card front">
    <div class="texture" role="img" aria-label="Soft navy background with a faint honeycomb texture"></div>
    <svg class="shapes" width="840" height="480" viewBox="0 0 840 480" aria-hidden="true">
      <line x1="0" y1="405" x2="840" y2="405" stroke="var(--gold)" stroke-width="1.5"/>
      <polygon points="135,383 685,383 705,405 685,428 135,428 115,405" fill="var(--gold)"/>
    </svg>
    <div class="brand-name">Heron</div>
    <div class="web">www.heronloans.com</div>
  </section>

  <section class="card card--back" aria-label="Card back">
    <div class="texture" role="img" aria-label="Soft white background with a faint honeycomb texture"></div>
    <svg class="shapes" width="840" height="480" viewBox="0 0 840 480" aria-hidden="true">
      <polygon points="510,0 840,0 840,26 532,26" fill="var(--gold)"/>
      <polygon points="52,0 75,0 75,112 63.5,124 52,112" fill="var(--navy)"/>
      <circle cx="63.5" cy="90" r="5" fill="var(--gold)"/>
      <path d="M54 106 q9.5 -12 19 0 z" fill="var(--gold)"/>
      <g class="icon-phone" transform="translate(76 208)">
        <polygon points="-14,-23 14,-23 28,0 14,23 -14,23 -28,0" fill="var(--gold)"/>
        <polygon points="-11,-18 11,-18 22,0 11,18 -11,18 -22,0" fill="var(--navy)"/>
        <path d="M-7 -8 l4 -2 l3 5 l-2.5 2 q2 5 6 7 l2 -2.5 l5 3 l-2 4 q-14 -1 -15.5 -16.5z" fill="var(--gold)"/>
      </g>
      <g class="icon-pin" transform="translate(76 277)">
        <polygon points="-14,-23 14,-23 28,0 14,23 -14,23 -28,0" fill="var(--gold)"/>
        <polygon points="-11,-18 11,-18 22,0 11,18 -11,18 -22,0" fill="var(--navy)"/>
        <path d="M0 10 q-8 -8 -8 -13 a8 8 0 0 1 16 0 q0 5 -8 13z" fill="var(--gold)"/>
        <circle cx="0" cy="-3" r="3" fill="var(--navy)"/>
      </g>
      <g class="icon-send" transform="translate(76 350)">
        <polygon points="-14,-23 14,-23 28,0 14,23 -14,23 -28,0" fill="var(--gold)"/>
        <polygon points="-11,-18 11,-18 22,0 11,18 -11,18 -22,0" fill="var(--navy)"/>
        <polygon points="-9,1 9,-8 3,9 0,3" fill="var(--gold)"/>
      </g>
      <polygon points="0,415 500,415 525,480 0,480" fill="var(--gold)"/>
      <polygon points="610,376 840,376 840,480 545,480 520,415 595,415" fill="var(--navy)"/>
    </svg>
    <div class="holder">
      <div class="holder-name">Elias Whitford</div>
      <div class="holder-title">FOUNDER &amp; CEO</div>
    </div>
    <ul class="contact-list">
      <li class="contact-item" style="top:208px">(555)-214-3080</li>
      <li class="contact-item" style="top:277px">412 Harbor Ave N,<br>Bayview, FL 33000</li>
      <li class="contact-item" style="top:350px">info@heronloans.com</li>
    </ul>
    <div class="brand-name">Heron</div>
    <div class="web">www.heronloans.com</div>
  </section>

</main>
</body>
</html>
```